Local Flower Farm Needs Business Card Design

I need business cards designed for a flower farm based in Eudora, Kansas.
Business Info:
We are a local cut flower farm located in Eudora, Kansas, founded by Corinne Haldwick. What started as a passion for agriculture and search for more joy in daily life has blossomed into a small business dedicated to providing the community with beautiful, fresh, and sustainable flowers. We specialize in local, seasonal blooms, ensuring that every petal reflects the care and dedication we pour into our craft. Our mission is to deliver the highest quality flowers directly to our customers through local farmers markets and to florists who share our commitment to sustainability. Join us in celebrating the beauty of nature, one bloom at a time!
Contact Details:
Corinne Haldwick
Owner
Phone 913-555-0147
Facebook: Rosalind Thorpe Gardens
Instagram: @RosalindThorpeGardens
Website: RosalindThorpeGardens.example
Target Market(s)
Wholesale to Florists and Direct to Consumer via Farmers Market
Industry/Entity Type
Florist, Farm
Contact Information for Business Card
Name, Contact Info, Logo
Look and feel
Each slider illustrates characteristics of the customer's brand and the style your logo design should communicate.

```html
<!DOCTYPE html>
<html lang="en">
<head>
<meta charset="utf-8">
<title>Rosalind Thorpe Gardens – Business Card</title>
<link href="https://fonts.googleapis.com/css2?family=Cormorant+Garamond:wght@500&family=Roboto:wght@400;700&display=swap" rel="stylesheet">
<style>
  :root {
    --backdrop: #1c1e20;
    --card: #0f3538;
    --card-deep: #0b2a2d;
    --ink: #f2f4f3;
    --ink-soft: #b9c6c5;
    --deboss: #0a2629;
  }
  * { margin: 0; padding: 0; box-sizing: border-box; }
  html, body { width: 1200px; height: 900px; overflow: hidden; }
  body {
    background: var(--backdrop);
    font-family: "Roboto", Arial, sans-serif;
    position: relative;
  }
  .card {
    position: absolute;
    background: var(--card);
    border-radius: 4px;
    box-shadow: 0 18px 40px rgba(0,0,0,.55);
    overflow: hidden;
  }
  /* front: portrait */
  .card-front {
    left: 110px; top: 150px;
    width: 340px; height: 595px;
  }
  .front-brand {
    position: absolute; left: 30px; top: 34px;
    display: flex; align-items: center; gap: 10px;
  }
  .brand-circle {
    width: 18px; height: 18px; border-radius: 50%;
    border: 1.5px solid var(--ink);
    flex: none;
  }
  .brand-name {
    font-family: "Cormorant Garamond", Georgia, serif;
    font-weight: 500;
    color: var(--ink);
    letter-spacing: .12em;
    text-transform: uppercase;
  }
  .front-brand .brand-name { font-size: 14px; }
  .holder { position: absolute; left: 30px; top: 92px; color: var(--ink); }
  .holder-name {
    font-weight: 700; font-size: 21px; letter-spacing: .02em;
    text-transform: uppercase;
  }
  .holder-role { font-size: 12px; color: var(--ink-soft); margin-top: 3px; }
  .holder-rule { width: 14px; height: 1px; background: var(--ink-soft); margin-top: 10px; }
  .contacts {
    list-style: none; position: absolute; left: 30px; top: 160px;
    color: var(--ink); font-size: 14px;
  }
  .contacts li { display: flex; align-items: center; gap: 8px; margin-bottom: 7px; }
  .contacts svg { width: 11px; height: 11px; flex: none; }
  .monogram-area {
    position: absolute; right: -40px; bottom: -40px;
    width: 300px; height: 300px; border-radius: 50%;
    background: radial-gradient(circle at 40% 35%, #12393c, var(--deboss));
    box-shadow: inset 6px 8px 16px rgba(0,0,0,.45), inset -3px -3px 8px rgba(255,255,255,.04);
  }
  /* back: landscape */
  .card-back {
    left: 520px; top: 150px;
    width: 580px; height: 332px;
    background: linear-gradient(160deg, var(--card), var(--card-deep));
  }
  .back-brand {
    position: absolute; inset: 0;
    display: flex; align-items: center; justify-content: center; gap: 14px;
  }
  .back-brand .brand-circle { width: 26px; height: 26px; border-width: 2px; }
  .back-brand .brand-name { font-size: 24px; }
</style>
</head>
<body>
  <section class="card card-front" aria-label="Business card front">
    <div class="front-brand">
      <span class="brand-circle"></span>
      <span class="brand-name">Rosalind Thorpe Gardens</span>
    </div>
    <div class="holder">
      <div class="holder-name">Corinne Haldwick</div>
      <div class="holder-role">Owner</div>
      <div class="holder-rule"></div>
    </div>
    <ul class="contacts">
      <li>
        <svg viewBox="0 0 24 24" fill="var(--ink)"><path d="M6.6 10.8a15 15 0 0 0 6.6 6.6l2.2-2.2a1 1 0 0 1 1-.25 11.4 11.4 0 0 0 3.6.57 1 1 0 0 1 1 1V20a1 1 0 0 1-1 1A17 17 0 0 1 3 4a1 1 0 0 1 1-1h3.5a1 1 0 0 1 1 1c0 1.25.2 2.45.57 3.6a1 1 0 0 1-.25 1z"/></svg>
        913-555-0147
      </li>
      <li>
        <svg viewBox="0 0 24 24"><circle cx="12" cy="12" r="11" fill="var(--ink)"/></svg>
        Rosalind Thorpe Gardens
      </li>
      <li>
        <svg viewBox="0 0 24 24" fill="none" stroke="var(--ink)" stroke-width="2.5"><circle cx="12" cy="12" r="10"/></svg>
        @RosalindThorpeGardens
      </li>
      <li>
        <svg viewBox="0 0 24 24" fill="none" stroke="var(--ink)" stroke-width="2"><circle cx="12" cy="12" r="10"/><path d="M2 12h20M12 2c3 3 3 17 0 20M12 2c-3 3-3 17 0 20"/></svg>
        RosalindThorpeGardens.example
      </li>
    </ul>
    <div class="monogram-area" role="img" aria-label="Debossed floral monogram decoration"></div>
  </section>

  <section class="card card-back" aria-label="Business card back">
    <div class="back-brand">
      <span class="brand-circle"></span>
      <span class="brand-name">Rosalind Thorpe Gardens</span>
    </div>
  </section>
</body>
</html>
```